Cruise Booking Website

Cruise search and booking website

This project is a redesign of a cruise booking website we did a few years ago.

The current website is located here: http://voyage.pylonworks.example/en/

It's not fully functional but gives you ad idea how miserable the old design was.

All the information about cruises, cruise lines, destinations, ports and shore excursions will be similar to http://www.sailquest.example/
Actual search pages (form, results, single result, sailing and cabin selection, ship info, booking) will have EXACTLY the same info as sailquest.example

We like the style of http://harborfleetdesk.example, it's quite modern, good spacing, not overloaded with information. So you can use it as an example of what we like, not what we want as a final result for us. Please, don't copy it. The result should not be possible to resemble the harborfleetdesk.example, because our site has to be unique. This is important!
If you submit a design that clearly reminds another cruise site it will be rejected!

Also the mockup provided is just to give you the basic structure and show what information has to be present on the page. It doesn't mean the layout has to be the same as a mockup. The layout is up to the designer.

I've updated the mockup to be more generic so it doesn't confuse you:
https://files.boxvault.example/s/k7m2qp9wz4hx/Home%20page.png

When you're adding social sharing icons like plazanet/chirpline you have to use chinese ones instead:
https://files.boxvault.example/s/t3nr8vx5lc2e/chinese-social-icons.png
Originals: http://minilk.example/qR7t

We'll start with home page first and after it's approved inner pages can be designed.

I know the cost of the project doesn't look high, but the task is straight forward and doesn't require to be very original, it's better to follow existing design and layout patterns that proved to work well.
That's why I encourage you to choose a template to build the design on top of one of https://themeparlor.example/ themes if it will save the design work, will be easier and faster for you. So it will be more like a customization than a new design from scratch.

Mockups, site map and logo files:
- https://files.boxvault.example/sh/h48dm2rs73fkpw/QvnbW2Xz8e

Website tree:
- https://sheets.papernest.example/document/d/7xPqR2mLw9sTk4VbN8cHj3YzA6eUf5GdKo1iMnBv/edit?usp=sharing
Updates

So far a lot of designs are just copying http://www.harborfleetdesk.example/ - we don't like it!

We like the style of harborfleetdesk.example, it's quite modern, good spacing, not overloaded with information. So you can use it as an example of what we like, not what we want as a final result for us. Please, don't copy it. The result should not be possible to resemble the harborfleetdesk.example, because our site has to be unique. This is important!

Target Market(s)

Chinese travellers

Industry/Entity Type

Build

Requirements
Must have
• * White, blue and red
* Large spacing, not too much information cramped into a small space like sailquest.example or the current website
* More "hidden" info in popups, tabs and so on, so not to many things are visible at the same time
* Compatible with kestrel scaffold styling (for easier coding):
- http://kestrelkit.codeshelf.example/scaffold/index.html
- http://skinmarket.example/
* Feel free to propose to build the design on top of one of https://themeparlor.example/ themes if it will save the design work, will be easier and faster for you

```html
<!DOCTYPE html>
<html lang="en">
<head>
<meta charset="utf-8">
<title>Bluewake Cruises – Home</title>
<link href="https://fonts.googleapis.com/css2?family=Ubuntu:wght@400;500&display=swap" rel="stylesheet">
<style>
:root{
  --sky-top:#0b4fb0;
  --sky-mid:#3f8fdc;
  --sky-low:#9cc8ef;
  --brand:#1d66b4;
  --brand-dark:#174f8e;
  --nav-top:#2f86d6;
  --nav-bottom:#1b62b0;
  --footer:#2a87e0;
  --footer-bar:#1f72c6;
  --panel:#2b5d98;
  --red:#d81e1e;
  --ink:#4a4a4a;
  --muted:#6b6b6b;
  --line:#e3e3e3;
  --white:#ffffff;
  --search-bg:rgba(40,40,40,.82);
  --button:#2f86d6;
}
*{box-sizing:border-box;margin:0;padding:0}
html,body{width:917px;height:1200px;overflow:hidden}
body{font-family:"Ubuntu",sans-serif;font-size:10px;color:var(--ink);position:relative}
.sky{position:absolute;inset:0;background:linear-gradient(180deg,var(--sky-top) 0%,var(--sky-mid) 45%,var(--sky-low) 100%)}
.page{position:absolute;left:84px;top:23px;width:749px;height:1177px;background:var(--white)}
.abs{position:absolute}

/* header */
.logo{left:10px;top:20px;display:flex;align-items:center;gap:8px}
.logo-dot{width:40px;height:40px;border-radius:50%;background:var(--brand)}
.logo-name{font-size:30px;font-weight:500;color:var(--brand);line-height:1}
.logo-url{position:absolute;left:48px;top:36px;font-size:9px;color:var(--brand);font-weight:500;letter-spacing:.5px}
.util{right:9px;top:18px;font-size:9.5px;color:var(--brand)}
.util span{margin:0 4px;color:#8aa}
.hotline{right:9px;top:45px;font-size:14px;color:var(--brand)}
.hotline b{font-weight:400;margin-left:10px}

/* nav */
.nav{left:8px;top:84px;width:731px;height:33px;background:linear-gradient(var(--nav-top),var(--nav-bottom));display:flex;align-items:center;padding-left:7px;border-radius:2px}
.nav a{color:var(--white);font-size:10px;text-decoration:none;font-weight:500;margin-right:20px;white-space:nowrap}
.nav a:last-of-type{margin-right:0}
.nav-search{position:absolute;right:4px;top:3px;width:144px;height:26px;background:var(--white);border:1px solid #bcd}
.nav-search svg{position:absolute;right:6px;top:6px}

/* hero */
.hero{left:0;top:117px;width:749px;height:342px;background:linear-gradient(135deg,#8a5a2c 0%,#c9a15c 35%,#3e9cc8 60%,#78c3dd 80%,#d9cfb4 100%)}
.finder{left:520px;top:145px;width:184px;height:274px;background:var(--search-bg);color:var(--white);padding:6px 7px}
.finder h2{font-size:14px;font-weight:400;border-bottom:1px solid rgba(255,255,255,.2);padding-bottom:5px;margin:0 -7px 8px;padding-left:7px}
.finder label{display:block;font-size:10px;font-weight:500;margin-bottom:3px}
.finder .sub{font-size:9.5px;font-weight:400}
.select{height:20px;background:linear-gradient(#fff,#e6e6e6);border-radius:2px;color:#333;font-size:9px;line-height:20px;padding-left:5px;position:relative;margin-bottom:8px}
.select::after{content:"";position:absolute;right:0;top:0;width:18px;height:20px;border-left:1px solid #bbb;background:linear-gradient(#f2f2f2,#d6d6d6)}
.select i{position:absolute;right:6px;top:5px;width:0;height:0;border:3px solid transparent;border-bottom-color:#777;z-index:1}
.select i+i{top:11px;border-bottom-color:transparent;border-top-color:#777}
.row{display:flex;gap:12px}
.row>div{flex:1}
.check{display:flex;align-items:center;gap:5px;font-size:10px;margin:4px 0 8px}
.check span{width:11px;height:11px;background:#ddd;border-radius:2px}
.btn{display:block;margin:0 auto;width:115px;height:24px;background:linear-gradient(#3d95e4,#1f6fc0);color:var(--white);font-size:11px;text-align:center;line-height:24px;font-weight:500}
.tabs{left:0;top:435px;height:24px;display:flex}
.tabs span{background:var(--button);color:var(--white);font-size:11px;font-weight:500;line-height:24px;padding:0 14px 0 8px;margin-right:-6px;clip-path:polygon(0 0,calc(100% - 10px) 0,100% 100%,0 100%)}
.tabs span:not(:first-child){clip-path:polygon(0 0,calc(100% - 10px) 0,100% 100%,10px 100%);padding-left:18px}

/* content */
.photo-frame{left:9px;top:476px;width:254px;height:241px;border:1px solid var(--line);background:var(--white);box-shadow:0 1px 3px rgba(0,0,0,.1)}
.photo{position:absolute;left:8px;top:8px;width:237px;height:224px;background:linear-gradient(160deg,#6f9fc9,#d8c6a2 55%,#3a9ab5)}
.dots{left:11px;top:740px;display:flex;gap:5px}
.dots i{width:9px;height:9px;border-radius:50%;background:#888}
.dots i:first-child{background:#b8865a}
.divider{left:9px;top:757px;width:618px;height:1px;background:var(--line)}
.promises{left:276px;top:477px;width:272px}
.promises h1{font-size:17px;font-weight:500;color:var(--brand);margin-bottom:6px}
.promises p{font-size:9.2px;line-height:14.5px;color:var(--muted);margin-bottom:13px}
.promises ul{list-style:none}
.promises li{font-size:9.3px;color:var(--muted);height:23.8px;display:flex;gap:10px}
.promises li::before{content:"";width:0;height:0;margin-top:2px;border:4px solid transparent;border-left:7px solid var(--brand);border-right:0}
.win{left:557px;top:479px;width:184px;height:77px;background:var(--red);color:var(--white);text-align:center;padding-top:6px}
.win .l1{font-size:13px}
.win .l1 b{font-size:16px;font-weight:400}
.win .l2{font-size:20px;line-height:25px}
.win .l3{font-size:16px}
.signup{left:557px;top:564px;width:184px;height:192px;background:var(--panel);padding:9px 9px;color:var(--white)}
.signup p{font-size:9.5px;line-height:12.5px;margin-bottom:10px}
.field{height:23px;background:var(--white);color:#888;font-size:8.5px;line-height:23px;padding-left:6px;margin-bottom:8px;border:1px solid #c9d6e6}
.signup .btn{width:93px;height:23px;line-height:23px;margin-top:5px;font-size:10px}

/* footer */
.footer{left:0;top:780px;width:749px;height:396px;background:var(--footer)}
.col{position:absolute;width:169px;color:var(--white)}
.col h3{font-size:12px;font-weight:400;padding-bottom:6px;border-bottom:1px solid rgba(255,255,255,.3);margin-bottom:6px}
.col ul{list-style:none}
.col li{font-size:9.3px;line-height:16.8px}
.f-news{background:var(--panel);padding:6px 7px;height:181px}
.f-news h3{border:0;margin-bottom:2px}
.f-news p{font-size:8px;line-height:11px;margin-bottom:5px}
.f-news .field{height:20px;line-height:20px;font-size:8px;margin-bottom:3px}
.f-news .btn{width:92px;height:23px;line-height:23px;font-size:10px;margin-top:7px;border:1px solid #9cc}
.badge{background:var(--white);display:flex;align-items:center;justify-content:center;gap:4px;color:var(--brand);font-weight:500}
.badge i{border-radius:50%;background:var(--brand)}
.contact p{font-size:9.3px;line-height:16.8px}
.social li{display:flex;align-items:center;gap:9px;padding-left:6px}
.social li::before{content:"";width:7px;height:7px;background:var(--white)}
.about p{font-size:8.8px;line-height:12px;text-align:justify}
.bottom{left:0;top:1153px;width:749px;height:24px;background:var(--footer-bar);color:var(--white);font-size:9.3px;line-height:24px;padding:0 12px}
.bottom span{margin:0 6px}
.bottom .copy{position:absolute;right:12px;top:0}
</style>
</head>
<body>
<div class="sky" role="img" aria-label="Blue sky with scattered white clouds"></div>
<div class="page">
  <header>
    <div class="abs logo"><span class="logo-dot"></span><span class="logo-name">Bluewake</span><span class="logo-url">www.bluewake.example</span></div>
    <div class="abs util">Location Finder<span>|</span>My Account<span>|</span>Sign In<span>|</span>Sign Up</div>
    <div class="abs hotline">Hotline<b>4008 512 309</b></div>
    <nav class="abs nav">
      <a>Home</a><a>Destinations</a><a>Cruise Lines</a><a>Shore Executions</a><a>Cruise Info</a><a>Deals</a><a>Online Booking</a><a>Contact Us</a>
      <div class="nav-search"><svg width="12" height="12" viewBox="0 0 12 12"><circle cx="5" cy="5" r="3.5" fill="none" stroke="#999" stroke-width="1.3"/><line x1="7.5" y1="7.5" x2="11" y2="11" stroke="#999" stroke-width="1.6"/></svg></div>
    </nav>
  </header>

  <section>
    <div class="abs hero" role="img" aria-label="Straw sun hat resting on a wooden deck chair by a turquoise sea and sandy beach"></div>
    <form class="abs finder">
      <h2>FIND YOUR CRUISE</h2>
      <label>Destination</label>
      <div class="select">Popular Destinations<i></i><i></i></div>
      <div class="row">
        <div><label>Length</label><div class="select">Any Length<i></i><i></i></div></div>
        <div><label>Month</label><div class="select">Any Month<i></i><i></i></div></div>
      </div>
      <label>Cruise Line</label>
      <div class="select">Any Cruise Line<i></i><i></i></div>
      <label>Number of Travelers</label>
      <div class="row">
        <div><label class="sub">Age 25+</label><div class="select">Any Length<i></i><i></i></div></div>
        <div><label class="sub">Age 25+</label><div class="select">Any Month<i></i><i></i></div></div>
      </div>
      <div class="check"><span></span>Check for senior rates</div>
      <span class="btn">SEARCH CRUISES</span>
    </form>
    <div class="abs tabs"><span>BOOK WITH US</span><span>DEALS</span><span>PACKAGES</span><span>NEWS</span><span>FIRST TIME CRUISER?</span></div>
  </section>

  <main>
    <div class="abs photo-frame"><div class="photo" role="img" aria-label="Couple taking a photo together at the rail of a cruise ship deck"></div></div>
    <div class="abs dots"><i></i><i></i><i></i></div>
    <div class="abs divider"></div>
    <article class="abs promises">
      <h1>Our Promises</h1>
      <p>Lorem ipsum dolor sit amet, consectetur adipisicing elit, sed do eiusmod tempor incididunt ut labore et dolore magna aliqua.Ut enim ad minim veniam, quis nostrud exercitation ullamco laboris</p>
      <ul>
        <li>Lorem ipsum dolor sit amet,</li>
        <li>consectetur adipisicing elit</li>
        <li>sed do eiusmod tempor inci</li>
        <li>labore et dolore magna aliq</li>
        <li>Ut enim ad minim veniam</li>
        <li>quis nostrud exercitation ullam</li>
      </ul>
    </article>
    <div class="abs win"><div class="l1">Enter To Win a <b>$3000</b></div><div class="l2">Cruise Vacation</div><div class="l3">For a couple</div></div>
    <form class="abs signup">
      <p>Sign up for our newsletter and receive our best deals in your inbox.</p>
      <div class="field">First Name</div>
      <div class="field">Email</div>
      <div class="field">Phone Number</div>
      <div class="field">Postal /Zip</div>
      <span class="btn">SUBSCRIBE</span>
    </form>
  </main>

  <footer class="abs footer">
    <div class="col" style="left:8px;top:19px"><h3>Popular Cruise Lines</h3><ul><li>Festiva Cruise Lines</li><li>Starlit Cruises</li><li>Riviera Cruises</li><li>Storybook Cruise Line</li><li>Lowland Atlantic Line</li><li>Meridian Cruises</li><li>Fjordway Cruise Line</li><li>Duchess Cruises</li><li>See More</li></ul></div>
    <div class="col" style="left:196px;top:19px"><h3>All About Cruising</h3><ul><li>Frequently Asked Questions</li><li>First Time Cruisers</li><li>Value Comparison</li><li>Cruising with Kids</li><li>Vacation Packing Guide</li><li>Onboard Activities</li><li>Theme Cruises</li><li>Special Event Cruises</li><li>See More</li></ul></div>
    <form class="col f-news" style="left:385px;top:19px">
      <h3>Free E-newsletter</h3>
      <p>Sign up for our newsletter and receive our best deals in your inbox.</p>
      <div class="field">First Name</div><div class="field">Email</div><div class="field">Phone</div><div class="field">Pin/Zip</div>
      <span class="btn">SUBSCRIBE</span>
    </form>
    <div class="col contact" style="left:572px;top:19px">
      <h3>Contact Us Today</h3>
      <div class="badge" style="width:77px;height:64px;font-size:10px"><i style="width:12px;height:12px"></i>Bluewake</div>
      <p style="margin-top:12px">BLUEWAKE CRUISES</p>
      <p>Hotline : 4008 512 309</p>
      <p>Book online or call</p>
      <p>Monday to Friday :: 9:00AM-18:00PM</p>
    </div>
    <div class="col" style="left:8px;top:219px"><h3>Popular Destinations</h3><ul><li>Alaska</li><li>Caribbean</li><li>Europe</li><li>Hawaii</li><li>Mexico</li><li>Duchess Cruises</li><li>See More</li></ul></div>
    <div class="col" style="left:196px;top:219px"><h3>Land Vacations</h3><ul><li>Hotels</li><li>Flights</li><li>Car Rentals</li><li>Vacation Packages</li><li>Shore Excursions</li><li>Car Rentals</li><li>See More</li></ul></div>
    <div class="col" style="left:384px;top:219px"><h3>Cruise by Type</h3><ul><li>Popular Cruises</li><li>Luxury Cruises</li><li>See More</li></ul>
      <h3 style="border:0;margin-top:5px">Join Our Community</h3>
      <ul class="social"><li>Like us on Plazanet</li><li>Follow us on Chirpline</li></ul>
    </div>
    <div class="col about" style="left:572px;top:219px">
      <h3>About BLUEWAKE</h3>
      <div class="badge" style="width:58px;height:41px;font-size:8px"><i style="width:8px;height:8px"></i>Bluewake</div>
      <p style="margin-top:12px">"Lorem ipsum dolor sit amet, consectetur adipisicing elit, sed do eiusmod tempor incididunt ut labore et dolore magna aliqua. aboris nisi ut aliquip e</p>
    </div>
  </footer>
  <div class="abs bottom">Terms of Use<span>|</span>Privacy<span>|</span>Legal<span>|</span>Site Map<span>|</span>Reset Location<span>|</span>Feedback<span class="copy">© 2013 Bluewake Cruises| All Rights Reserved.</span></div>
</div>
</body>
</html>
```